Web design for Money Service Business (uncoded)

We need a very basic website with 5-6 pages. Home page, Services, Transfer(How to use our service), About us, Contact us, FAQ
Our company name is Norvane Exchange. We are a company that deals with currency exchange and international money transfer. We do cash exchange and international money transfers to bank accounts all over the world. We offer highly competitive exchange rates so usually attract customers who transfer money over $10,000. Our niche is with larger sums of money, the design needs to be professional and communicate trust, security and stability.

```html
<!DOCTYPE html>
<html lang="en">
<head>
<meta charset="utf-8">
<title>Norvane Exchange – International Money Transfer</title>
<link href="https://fonts.googleapis.com/css2?family=Open+Sans:wght@400;600;700&family=Roboto:wght@400;500&display=swap" rel="stylesheet">
<style>
:root{
  --blue:#1d5a8e;
  --blue-dark:#16466f;
  --orange:#f7931e;
  --orange-light:#ffa733;
  --dark:#1c2125;
  --text:#555;
  --heading:#333;
  --rule:#cfcfcf;
  --white:#fff;
}
*{margin:0;padding:0;box-sizing:border-box}
html,body{width:898px;height:1200px;overflow:hidden;background:var(--white)}
body{position:relative;font-family:"Open Sans",sans-serif;color:var(--text)}
.abs{position:absolute}
a{text-decoration:none;color:inherit}

/* header */
.brand{left:106px;top:12px}
.brand-name{font-family:"Open Sans",sans-serif;font-weight:700;font-size:22px;color:var(--blue);letter-spacing:.5px;line-height:24px}
.brand-tag{font-size:7.5px;letter-spacing:2.4px;color:var(--blue);margin-top:2px}
.social{display:flex;gap:4px}
.social span{width:15px;height:15px;border-radius:2px;display:block}
.social .s1{background:#c8232c}.social .s2{background:#3b5998}.social .s3{background:#2f8fc9}.social .s4{background:#555}
.social.top{left:714px;top:8px}
.phone{left:692px;top:33px;font-family:"Roboto",sans-serif;font-weight:500;font-size:11px;color:var(--blue);display:flex;align-items:center;gap:4px}

/* nav + hero */
.nav{left:0;top:58px;width:898px;height:40px;background:var(--dark);display:flex;justify-content:center;gap:20px;align-items:center;font-family:"Roboto",sans-serif;font-size:10.5px;color:var(--white);z-index:2}
.nav .active,.foot-nav .active{color:var(--orange)}
.hero{left:0;top:84px;width:898px;height:271px;background:radial-gradient(ellipse at 62% 45%,#c9c6b4 0%,#8b8c7d 35%,#3e403c 70%,#1f201f 100%)}
.hero-title{left:106px;top:169px;width:274px;height:35px;background:rgba(20,20,20,.85);color:var(--orange);font-family:"Roboto",sans-serif;font-size:14.5px;line-height:35px;padding-left:10px;white-space:nowrap}
.hero-sub{left:106px;top:206px;width:168px;height:36px;background:rgba(240,240,240,.88);color:var(--blue);font-family:"Roboto",sans-serif;font-size:14.5px;line-height:36px;padding-left:14px}
.btn{background:linear-gradient(var(--orange-light),var(--orange));color:#222;font-weight:600;font-size:8.5px;text-align:center;box-shadow:0 1px 2px rgba(0,0,0,.3)}
.hero-btn{left:106px;top:271px;width:85px;height:25px;line-height:25px}

/* services */
.service{width:160px;text-align:center}
.service svg{display:block;margin:0 auto}
.service h3{font-family:"Roboto",sans-serif;font-weight:400;font-size:11.5px;color:var(--heading);margin-top:12px}
.service p{font-size:8.3px;line-height:15px;margin-top:4px}
.service .more{margin-top:6px}

/* about */
.about-media{left:106px;top:574px;width:285px;height:180px;background:linear-gradient(160deg,#e9e3d3 0%,#b79c7a 45%,#6d3b1f 80%,#4a2512 100%)}
.about-title{left:421px;top:569px;font-family:"Roboto",sans-serif;font-weight:500;font-size:13px;color:var(--heading)}
.about-text{left:421px;top:592px;width:365px;font-size:8.3px;line-height:10.5px}
.ticks{left:421px;top:651px;list-style:none;font-size:8.3px}
.ticks li{display:flex;align-items:center;gap:6px;height:22px}
.about-btn{left:421px;top:729px;width:85px;height:25px;line-height:25px}

/* member banner */
.banner{left:106px;top:798px;width:683px;height:72px;background:var(--blue);overflow:hidden}
.banner-lead{left:12px;top:26px;font-family:"Roboto",sans-serif;font-size:15px;color:var(--white);letter-spacing:.3px}
.banner-deal{left:164px;top:0;width:110px;height:72px;background:var(--orange);clip-path:polygon(27% 0,100% 0,73% 100%,0 100%)}
.deal-pct{left:190px;top:12px;font-family:"Roboto",sans-serif;font-size:27px;color:var(--blue-dark)}
.deal-word{left:190px;top:42px;font-family:"Roboto",sans-serif;font-weight:500;font-size:13px;color:var(--white)}
.benefits-title{left:279px;top:15px;font-weight:700;font-size:10px;color:var(--white)}
.benefits{top:31px;list-style:none;font-size:8.3px;color:var(--white)}
.benefits li{display:flex;align-items:center;gap:4px;height:15px}
.banner-btn{left:552px;top:26px;width:116px;height:24px;line-height:24px}

/* news + testimonials */
.section-title{font-family:"Roboto",sans-serif;font-weight:500;font-size:14px;color:var(--heading);padding-bottom:4px;border-bottom:1px solid var(--rule)}
.news-title{left:106px;top:910px;width:300px}
.testi-title{left:455px;top:910px;width:334px}
.news-thumb{left:106px;width:83px;height:59px}
.thumb-a{top:954px;background:linear-gradient(135deg,#f1f1f1,#9fc3e0 60%,#5d7d9b)}
.thumb-b{top:1042px;background:linear-gradient(135deg,#d8d5cc,#6c6a66 55%,#1f2a44)}
.news-body{left:198px;width:215px;font-size:8.3px;line-height:10.5px}
.news-body h4{font-weight:700;font-size:8.5px;color:var(--blue);margin-bottom:3px}
.news-body svg{margin-top:5px}
.testi-photo{left:440px;top:952px;width:112px;height:148px;background:linear-gradient(180deg,#fafafa 0%,#cfdff0 55%,#8fb2d6 100%)}
.quote{left:561px;top:963px;width:228px;height:71px;background:#6b6b6b;color:var(--white);font-size:8px;line-height:10.5px;padding:14px 10px}
.quote::after{content:"";position:absolute;left:12px;bottom:-12px;border-left:0 solid transparent;border-right:12px solid transparent;border-top:12px solid #6b6b6b}
.testi-name{left:578px;top:1058px;font-family:"Roboto",sans-serif;font-size:11.5px;color:var(--blue)}
.testi-name small{font-size:8px;color:#444;margin-left:3px}

/* footer */
.footer{left:0;top:1140px;width:898px;height:60px}
.foot-nav{left:0;top:1147px;width:898px;display:flex;justify-content:center;gap:11px;font-family:"Roboto",sans-serif;font-size:10.5px;color:var(--white)}
.copyright{left:106px;top:1177px;font-size:8px;color:var(--white)}
.social.bottom{left:714px;top:1171px}
</style>
</head>
<body>

<header>
  <div class="brand abs">
    <div class="brand-name">NORVANE EXCHANGE</div>
    <div class="brand-tag">INTERNATIONAL MONEY TRANSFER</div>
  </div>
  <div class="social top abs"><span class="s1"></span><span class="s2"></span><span class="s3"></span><span class="s4"></span></div>
  <div class="phone abs">
    <svg width="10" height="12" viewBox="0 0 10 12"><path d="M3 0 L5 3 L3.6 4.6 Q4.4 7 6.4 8.4 L8 7 L10 9.4 L8.4 11.6 Q2 10 0.6 2 Z" fill="var(--orange)"/></svg>
    1-800-555-0142
  </div>
</header>

<div class="hero abs" role="img" aria-label="Pile of banknotes on a dark backdrop"></div>
<nav class="nav abs">
  <a class="active">Home</a><a>Services</a><a>Transfer</a><a>About us</a><a>Contact us</a><a>FAQ</a>
</nav>
<div class="hero-title abs">Lorem ipsum dolor sit amet consectetur</div>
<div class="hero-sub abs">Adipisicing elit sed do</div>
<a class="btn hero-btn abs">Read more</a>

<section>
  <div class="service abs" style="left:103px;top:386px">
    <svg width="56" height="56" viewBox="0 0 56 56"><circle cx="28" cy="28" r="28" fill="var(--blue)"/><path d="M12 21 H40 M34 15 L42 21 L34 27 M44 35 H16 M22 29 L14 35 L22 41" stroke="#fff" stroke-width="5" fill="none" stroke-linejoin="round"/></svg>
    <h3>Money Exchange</h3>
    <p>Lorem ipsum dolor sit amet, consecte-tur adipisicing elit, sed do eiusmod tempor incididunt ut labore et dolore</p>
    <svg class="more" width="15" height="15" viewBox="0 0 15 15"><circle cx="7.5" cy="7.5" r="7.5" fill="var(--orange)"/><path d="M6 4 L9.5 7.5 L6 11" stroke="#fff" stroke-width="2" fill="none"/></svg>
  </div>
  <div class="service abs" style="left:278px;top:386px">
    <svg width="56" height="56" viewBox="0 0 56 56"><circle cx="28" cy="28" r="28" fill="var(--blue)"/><circle cx="28" cy="28" r="19" fill="none" stroke="#fff" stroke-width="4"/><text x="28" y="37" text-anchor="middle" font-family="Roboto,sans-serif" font-weight="500" font-size="26" fill="#fff">$</text></svg>
    <h3>Money Transfer</h3>
    <p>Lorem ipsum dolor sit amet, consecte-tur adipisicing elit, sed do eiusmod tempor incididunt ut labore et dolore</p>
    <svg class="more" width="15" height="15" viewBox="0 0 15 15"><circle cx="7.5" cy="7.5" r="7.5" fill="var(--orange)"/><path d="M6 4 L9.5 7.5 L6 11" stroke="#fff" stroke-width="2" fill="none"/></svg>
  </div>
  <div class="service abs" style="left:455px;top:386px">
    <svg width="56" height="56" viewBox="0 0 56 56"><circle cx="28" cy="28" r="28" fill="var(--blue)"/><rect x="19" y="17" width="15" height="25" rx="2" fill="none" stroke="#fff" stroke-width="2"/><line x1="19" y1="37" x2="34" y2="37" stroke="#fff" stroke-width="1.5"/><path d="M36 11 A6 6 0 0 1 42 17 M36 14 A3 3 0 0 1 39 17" stroke="#fff" stroke-width="1.5" fill="none"/></svg>
    <h3>Mobile Tranfer</h3>
    <p>Lorem ipsum dolor sit amet, consecte-tur adipisicing elit, sed do eiusmod tempor incididunt ut labore et dolore</p>
    <svg class="more" width="15" height="15" viewBox="0 0 15 15"><circle cx="7.5" cy="7.5" r="7.5" fill="var(--orange)"/><path d="M6 4 L9.5 7.5 L6 11" stroke="#fff" stroke-width="2" fill="none"/></svg>
  </div>
  <div class="service abs" style="left:631px;top:386px">
    <svg width="56" height="56" viewBox="0 0 56 56"><circle cx="28" cy="28" r="28" fill="var(--blue)"/><circle cx="28" cy="28" r="4" fill="#fff"/><path d="M20 20 A11 11 0 0 0 20 36 M36 20 A11 11 0 0 1 36 36 M15 15 A18 18 0 0 0 15 41 M41 15 A18 18 0 0 1 41 41" stroke="#fff" stroke-width="3.5" fill="none" stroke-linecap="round"/></svg>
    <h3>Online Money Tranfer</h3>
    <p>Lorem ipsum dolor sit amet, consecte-tur adipisicing elit, sed do eiusmod tempor incididunt ut labore et dolore</p>
    <svg class="more" width="15" height="15" viewBox="0 0 15 15"><circle cx="7.5" cy="7.5" r="7.5" fill="var(--orange)"/><path d="M6 4 L9.5 7.5 L6 11" stroke="#fff" stroke-width="2" fill="none"/></svg>
  </div>
</section>

<section>
  <div class="about-media abs" role="img" aria-label="Video of the company reception office"></div>
  <h2 class="about-title abs">About our company</h2>
  <p class="about-text abs">Lorem ipsum dolor sit amet, consectetur adipisicing elit, sed do eiusmod tempor incididunt ut labore et dolore magna aliqua. Ut enim ad minim veniam, quis nostrud exercitation ullamco laboris nisi ut aliquip ex ea commodo consequat. Duis aute irure dolor in reprehenderit in voluptate velit esse cillum dolore eu fugiat nulla pariatur. Excepteur sint</p>
  <ul class="ticks abs">
    <li><svg width="12" height="11" viewBox="0 0 12 11"><path d="M1 6 L4.5 10 L11 1" stroke="var(--blue)" stroke-width="2.4" fill="none"/></svg>Lorem ipsum dolor sit amet, consectetur adipisicing</li>
    <li><svg width="12" height="11" viewBox="0 0 12 11"><path d="M1 6 L4.5 10 L11 1" stroke="var(--blue)" stroke-width="2.4" fill="none"/></svg>elit, sed do eiusmod tempor incididunt ut labore et</li>
    <li><svg width="12" height="11" viewBox="0 0 12 11"><path d="M1 6 L4.5 10 L11 1" stroke="var(--blue)" stroke-width="2.4" fill="none"/></svg>dolore magna aliqua.</li>
  </ul>
  <a class="btn about-btn abs">Read more</a>
</section>

<section class="banner abs">
  <div class="banner-lead abs">Be a Member and get</div>
  <div class="banner-deal abs"></div>
  <div class="deal-pct abs">10%</div>
  <div class="deal-word abs">discount</div>
  <div class="benefits-title abs">More Benefits</div>
  <ul class="benefits abs" style="left:279px">
    <li><svg width="11" height="10" viewBox="0 0 11 10"><rect x=".5" y="1.5" width="8" height="8" fill="none" stroke="var(--orange)"/><path d="M2 5 L4.5 8 L10.5 .5" stroke="var(--orange)" stroke-width="2" fill="none"/></svg>Lorem ipsum dolor sit amet</li>
    <li><svg width="11" height="10" viewBox="0 0 11 10"><rect x=".5" y="1.5" width="8" height="8" fill="none" stroke="var(--orange)"/><path d="M2 5 L4.5 8 L10.5 .5" stroke="var(--orange)" stroke-width="2" fill="none"/></svg>consectetur adipisicing elit</li>
  </ul>
  <ul class="benefits abs" style="left:418px">
    <li><svg width="11" height="10" viewBox="0 0 11 10"><rect x=".5" y="1.5" width="8" height="8" fill="none" stroke="var(--orange)"/><path d="M2 5 L4.5 8 L10.5 .5" stroke="var(--orange)" stroke-width="2" fill="none"/></svg>sed do eiusmod tempor</li>
    <li><svg width="11" height="10" viewBox="0 0 11 10"><rect x=".5" y="1.5" width="8" height="8" fill="none" stroke="var(--orange)"/><path d="M2 5 L4.5 8 L10.5 .5" stroke="var(--orange)" stroke-width="2" fill="none"/></svg>Ut enim ad minim veniam,</li>
  </ul>
  <a class="btn banner-btn abs">Get you discount now</a>
</section>

<section>
  <h2 class="section-title news-title abs">News</h2>
  <div class="news-thumb thumb-a abs" role="img" aria-label="Man working on a laptop"></div>
  <article class="news-body abs" style="top:952px">
    <h4>Lorem ipsum dolor sit amet</h4>
    <p>Lorem ipsum dolor sit amet, consectetur adipisicing elit, sed do eiusmod tempor incididunt ut labore et dolore magna aliqua. Ut enim ad minim veniam, quis</p>
    <svg width="15" height="15" viewBox="0 0 15 15"><circle cx="7.5" cy="7.5" r="7.5" fill="var(--orange)"/><path d="M6 4 L9.5 7.5 L6 11" stroke="#fff" stroke-width="2" fill="none"/></svg>
  </article>
  <div class="news-thumb thumb-b abs" role="img" aria-label="Graduate in cap and gown"></div>
  <article class="news-body abs" style="top:1040px">
    <h4>consectetur adipisicing elit, sed do eiusmod</h4>
    <p>Lorem ipsum dolor sit amet, c tempor incididunt ut labore et dolore magna aliqua. Ut enim ad minim veniam, quis nostrud exercitation ullamco laboris nisi</p>
    <svg width="15" height="15" viewBox="0 0 15 15"><circle cx="7.5" cy="7.5" r="7.5" fill="var(--orange)"/><path d="M6 4 L9.5 7.5 L6 11" stroke="#fff" stroke-width="2" fill="none"/></svg>
  </article>
</section>

<section>
  <h2 class="section-title testi-title abs">Testimonials</h2>
  <div class="testi-photo abs" role="img" aria-label="Portrait of a smiling client in a blue shirt"></div>
  <blockquote class="quote abs">Lorem ipsum dolor sit amet, consectetur adipisicing elit, sed do eiusmod tempor incididunt ut labore et dolore magna aliqua. Ut enim ad minim veniam, quis nostrud exercitation ullamco laboris nisi ut aliquip ex</blockquote>
  <div class="testi-name abs">Marcus<small>Manager</small></div>
</section>

<footer>
  <svg class="footer abs" width="898" height="60" viewBox="0 0 898 60"><path d="M0 18 H64 Q84 18 94 8 Q102 0 116 0 H782 Q796 0 804 8 Q814 18 834 18 H898 V60 H0 Z" fill="var(--dark)"/></svg>
  <nav class="foot-nav abs">
    <a class="active">Home</a><a>Services</a><a>Transfer</a><a>About us</a><a>Contact us</a><a>FAQ</a>
  </nav>
  <div class="copyright abs">© 2013, Copy Right for Norvane Exchange</div>
  <div class="social bottom abs"><span class="s1"></span><span class="s2"></span><span class="s3"></span><span class="s4"></span></div>
</footer>

</body>
</html>
```